SkyvornQ Business Cards and Stationary Design

Need a design for our business cards and stationary. I want to carry on the theme of the logo. I want the business cards to have a design on the back. I would like the business cards and the stationary to carry the same theme, design scheme, and branding

Target Market(s)

Airlines and Maintenance Facilities

Industry/Entity Type

Aviation

Contact Information for Business Card

Name
Position Title
Address: 4827 Trellis Hollow Road, Fort Pierce, Florida, 34951
Office Number
Mobile Number
Email
Website

Font styles to use
Serif
Sans Serif

Colors

Designer to choose colors to be used in the design.

```html
<!DOCTYPE html>
<html lang="en">
<head>
<meta charset="utf-8">
<title>SkyvornQ Business Card</title>
<link href="https://fonts.googleapis.com/css2?family=Montserrat:wght@500;600;700&display=swap" rel="stylesheet">
<style>
  :root {
    --page-bg: #3b3b3d;
    --card-navy: #1e3366;
    --card-accent: #2b4278;
    --ink-light: #ffffff;
    --ink-soft: #dfe4ef;
  }
  * { box-sizing: border-box; margin: 0; padding: 0; }
  html, body {
    width: 1200px; height: 800px; overflow: hidden;
    background: var(--page-bg);
    font-family: "Montserrat", Arial, sans-serif;
    color: var(--ink-light);
  }
  .stage { position: relative; width: 1200px; height: 800px; }
  .card {
    position: absolute; top: 278px;
    width: 428px; height: 244px;
    background: var(--card-navy);
    overflow: hidden;
  }
  .card-front { left: 170px; border-radius: 10px; }
  .card-back { left: 606px; }
  .brand-circle {
    position: absolute; width: 230px; height: 230px; border-radius: 50%;
    background: var(--card-accent); opacity: 0.55;
  }
  .card-front .brand-circle { left: 310px; top: 7px; }
  .card-back .brand-circle { left: -115px; top: 7px; }
  .card-content { position: relative; }
  .person-name {
    position: absolute; left: 22px; top: 22px;
    font-size: 18px; font-weight: 500; letter-spacing: 0.2px;
  }
  .person-title {
    position: absolute; left: 22px; top: 46px;
    font-size: 11.5px; font-weight: 500;
  }
  .title-rule {
    position: absolute; left: 22px; top: 65px;
    width: 16px; height: 1px; background: var(--ink-soft);
  }
  .contact-list, .address {
    position: absolute; left: 22px;
    font-size: 11.5px; font-weight: 500; line-height: 14px;
    list-style: none; font-style: normal;
  }
  .contact-list { top: 92px; }
  .address { top: 177px; }
  .wordmark {
    position: absolute; left: 134px; top: 98px;
    font-size: 33px; font-weight: 700; letter-spacing: 5px;
    white-space: nowrap;
  }
  .back-web {
    position: absolute; left: 170px; top: 194px;
    font-size: 13px; font-weight: 600;
  }
</style>
</head>
<body>
<main class="stage">
  <section class="card card-front" aria-label="Business card front">
    <div class="brand-circle"></div>
    <div class="card-content">
      <h1 class="person-name">Dorian Vale</h1>
      <p class="person-title">Co-Owner</p>
      <div class="title-rule"></div>
      <ul class="contact-list">
        <li>Mobile: (555) 318-4720</li>
        <li>Phone: 555-207-6193</li>
        <li>Email: info@skyvornq.com</li>
        <li>Web: www.skyvornq.com</li>
      </ul>
      <address class="address">
        4827 Trellis Hollow Road,<br>
        Fort Pierce,<br>
        Florida, 34951
      </address>
    </div>
  </section>

  <section class="card card-back" aria-label="Business card back">
    <div class="brand-circle"></div>
    <div class="card-content">
      <p class="wordmark">SKYVORNQ</p>
      <p class="back-web">www.skyvornq.com</p>
    </div>
  </section>
</main>
</body>
</html>
```